Export company based in South America (Ecuador) we export flowers, chocolate, and bananas

We need a website that gives our potential clients and introduction into our company and the different types of commodities we export around the world. We are based in Quito, Ecuador so the website should portray the feel of Ecuadorian landscapes within a modern looking website.
At the moment we are exporting roses, chocolate, and bananas so the website should have an intro to our company and then three different areas that describe our three main commodity. The three different sections should explain why each of the products from Ecuador are some of the best in the world in their categories and the benefits of importing the commodity through our company.
Industry/Entity Type
Commodity
Number of Pages Required
4 page

```html
<!DOCTYPE html>
<html lang="en">
<head>
<meta charset="utf-8">
<title>Verdanta – Export Flowers, Chocolate &amp; Bananas</title>
<link href="https://fonts.googleapis.com/css2?family=Montserrat:wght@500;600;700;800&family=Lato:wght@400;700&display=swap" rel="stylesheet">
<style>
:root{
  --green:#4db811;
  --green-deep:#2f8700;
  --green-text:#3f7d12;
  --orange:#f7a100;
  --ink:#333;
  --muted:#6b6b6b;
  --paper:#ffffff;
  --mist:#f4f5f4;
  --footer:#3b3b3b;
  --footer-bar:#2f2f2f;
}
*{margin:0;padding:0;box-sizing:border-box}
html,body{width:1200px;height:3580px;overflow:hidden}
body{position:relative;background:var(--paper);font-family:'Lato',sans-serif;color:var(--ink)}
.abs{position:absolute}
.btn{position:absolute;display:flex;align-items:center;justify-content:center;background:var(--orange);color:#fff;font-family:'Montserrat',sans-serif;font-weight:600;border-radius:30px;text-decoration:none}

/* header */
.site-header{position:absolute;left:0;top:0;width:1200px;height:93px;background:#fff;border-bottom:1px solid #e6e6e6}
.brand{position:absolute;left:121px;top:22px;font-family:'Montserrat',sans-serif;font-weight:700;font-size:40px;color:var(--orange);display:flex;align-items:center;gap:10px}
.brand-dot{width:14px;height:14px;border-radius:50%;background:var(--green)}
.nav{position:absolute;left:418px;top:35px;display:flex;font-family:'Montserrat',sans-serif;font-weight:600;font-size:15px;color:#555}
.nav a{color:inherit;text-decoration:none;padding:0 22px;border-left:1px solid #ccc;line-height:20px}
.nav a:first-child{border-left:none;padding-left:0;color:var(--green-text)}

/* hero */
.hero{position:absolute;left:0;top:93px;width:1200px;height:640px;background:linear-gradient(180deg,#5a8fd0 0%,#b9cfe0 22%,#5f8a35 45%,#3f6e22 70%,#8a8a78 100%)}
.hero-title{position:absolute;left:0;top:290px;width:1200px;text-align:center;color:#fff;font-family:'Montserrat',sans-serif;font-weight:800;font-size:66px;text-shadow:0 2px 6px rgba(0,0,0,.35)}
.hero-sub{position:absolute;left:0;top:368px;width:1200px;text-align:center;color:#fff;font-family:'Montserrat',sans-serif;font-weight:700;font-size:34px;text-shadow:0 2px 6px rgba(0,0,0,.35)}
.arrow{position:absolute;top:325px}

/* about */
.section-title{position:absolute;left:0;width:1200px;text-align:center;font-family:'Montserrat',sans-serif;font-weight:700}
.about-title{top:737px;font-size:40px;color:var(--green-text)}
.about-title span{color:var(--orange)}
.about-copy{position:absolute;left:200px;width:800px;text-align:center;font-size:14px;line-height:23px;color:var(--muted)}
.product-ring{position:absolute;width:264px;height:264px;border-radius:50%;border:3px solid var(--green-text)}
.product-ring.alt{border-color:var(--orange)}
.product-photo{position:absolute;left:11px;top:11px;width:236px;height:236px;border-radius:50%}
.product-name{position:absolute;top:1230px;width:300px;text-align:center;font-family:'Montserrat',sans-serif;font-weight:600;font-size:30px;color:var(--green-text)}
.product-copy{position:absolute;top:1274px;width:300px;text-align:center;font-size:14.5px;line-height:21.5px;color:var(--muted)}

/* benefits */
.benefits-title{top:1574px;font-size:32px;color:#fff;font-weight:600}
.benefit-icon{position:absolute;width:94px;height:94px;border-radius:50%;border:2px solid #fff;display:flex;align-items:center;justify-content:center}
.benefit-name{position:absolute;font-family:'Montserrat',sans-serif;font-weight:600;font-size:22px;color:#fff}
.benefit-copy{position:absolute;width:340px;font-size:14.5px;line-height:21.5px;color:#fff}

/* why */
.why-photo{position:absolute;left:139px;top:2141px;width:436px;height:436px;border-radius:50%;background:#fff;box-shadow:0 4px 20px rgba(0,0,0,.1)}
.why-photo div{position:absolute;left:14px;top:14px;width:408px;height:408px;border-radius:50%;background:radial-gradient(circle at 45% 40%,#b6e23a 0%,#7fbf2a 45%,#5a60a8 85%)}
.why-title{position:absolute;left:607px;top:2180px;font-family:'Montserrat',sans-serif;font-weight:700;font-size:30px;color:var(--green-text)}
.why-copy{position:absolute;left:610px;top:2233px;width:460px;font-size:14.5px;line-height:25px;color:var(--muted)}
.why-item{position:absolute;width:220px}
.why-item svg{position:absolute;left:-28px;top:3px}
.why-item b{display:block;font-family:'Lato',sans-serif;font-weight:700;font-size:16px;color:#5b6b50;margin-bottom:2px}
.why-item p{font-size:14px;line-height:19px;color:var(--muted)}

/* blogs */
.blogs{position:absolute;left:0;top:2630px;width:1200px;height:563px;background:var(--mist)}
.blogs-title{position:absolute;left:139px;top:2697px;font-family:'Montserrat',sans-serif;font-weight:700;font-size:28px;color:var(--green-text)}
.blog-photo{position:absolute;top:2757px;width:301px;height:210px}
.blog-card{position:absolute;top:2929px;width:262px;height:173px;background:#fff;text-align:center;padding-top:22px}
.blog-date{font-family:'Montserrat',sans-serif;font-weight:600;font-size:13px;color:var(--orange)}
.blog-head{font-family:'Montserrat',sans-serif;font-weight:700;font-size:14px;line-height:22px;color:#222;margin-top:4px}
.blog-copy{font-size:13px;line-height:19px;color:var(--muted);margin-top:6px;padding:0 18px}
.blog-more{font-family:'Montserrat',sans-serif;font-weight:700;font-size:11px;color:var(--green-text);margin-top:12px}

/* footer */
.site-footer{position:absolute;left:0;top:3193px;width:1200px;height:327px;background:var(--footer);color:#e6e6e6}
.foot-head{position:absolute;top:72px;font-family:'Montserrat',sans-serif;font-weight:700;font-size:18px;color:#fff}
.foot-menu{position:absolute;left:160px;top:110px;font-size:14.5px;line-height:23px;list-style:none}
.contact-row{position:absolute;left:332px;display:flex;gap:10px;font-size:14.5px;line-height:18px}
.contact-row i{width:34px;height:34px;border-radius:50%;background:var(--green);display:flex;align-items:center;justify-content:center;flex:none}
.foot-sub{position:absolute;left:619px;top:110px;font-size:14.5px}
.foot-input{position:absolute;left:619px;top:136px;width:224px;height:38px;background:#fff;font-size:10px;color:#666;padding:13px 12px}
.foot-btn{position:absolute;left:619px;top:187px;width:116px;height:32px;background:var(--green);color:#fff;font-family:'Montserrat',sans-serif;font-weight:700;font-size:13px;display:flex;align-items:center;justify-content:center}
.social{position:absolute;left:906px;display:flex;gap:10px;align-items:center}
.social i{width:38px;height:38px;border-radius:50%;border:2px solid #fff}
.social small{display:block;font-size:10px;color:#ccc}
.social span{font-size:14.5px;line-height:16px}
.copyright{position:absolute;left:0;top:3520px;width:1200px;height:60px;background:var(--footer-bar);color:var(--orange);font-size:14px;text-align:center;line-height:60px}
</style>
</head>
<body>

<header class="site-header">
  <div class="brand"><span class="brand-dot"></span>Verdanta</div>
  <nav class="nav">
    <a href="#">About Us</a><a href="#">What We Export</a><a href="#">Why We Are</a><a href="#">Blogs</a><a href="#">Contact Us</a>
  </nav>
</header>

<section class="hero" role="img" aria-label="Green Andean valley with a rocky river under a blue sky"></section>
<svg class="abs" style="left:0;top:640px" width="1200" height="95" viewBox="0 0 1200 95">
  <path fill="#fff" d="M0,95 L0,70 Q600,10 1200,70 L1200,95 Z"/>
</svg>
<svg class="arrow" style="left:66px" width="26" height="52" viewBox="0 0 26 52"><polyline points="23,2 3,26 23,50" fill="none" stroke="#fff" stroke-width="4"/></svg>
<svg class="arrow" style="left:1128px" width="26" height="52" viewBox="0 0 26 52"><polyline points="3,2 23,26 3,50" fill="none" stroke="#fff" stroke-width="4"/></svg>
<h1 class="hero-title">Welcome to Verdanta</h1>
<p class="hero-sub">Eport Flowers, Chocolate, &amp; Bananas</p>
<a class="btn" href="#" style="left:505px;top:424px;width:195px;height:56px;font-size:19px">Learn More</a>

<h2 class="section-title about-title">About <span>Verdanta</span></h2>
<p class="about-copy" style="top:799px">Fusce tellus Sed metus augue convallis et vehicula ut pulvinar eu ante Integer orci tellus tristique vitae consequat nec porta vel lectus Nulla sit amet diam aliquam enim Proin dui lectus cursus eu mattis laoreet viverra</p>
<p class="about-copy" style="top:858px">sit amet quam Curabitur vel dolor ultrices ipsum dictum tristique Praesent vitae lacus Ut velit enim vestibulum non fermentum nec hendrerit quis leo Pellentesque rutrum malesuada neque</p>

<div class="product-ring" style="left:134px;top:957px"><div class="product-photo" role="img" aria-label="Bouquet of roses and mixed flowers" style="background:radial-gradient(circle,#e8384a,#f08a1c 50%,#8a3fae)"></div></div>
<div class="product-ring alt" style="left:464px;top:957px"><div class="product-photo" role="img" aria-label="Assorted chocolate truffles" style="background:radial-gradient(circle,#9a6040,#5a3120 60%,#2e1a10)"></div></div>
<div class="product-ring" style="left:794px;top:957px"><div class="product-photo" role="img" aria-label="Bunch of ripe bananas on the plant" style="background:radial-gradient(circle,#e8c23a,#c9a21a 45%,#5fae2a)"></div></div>

<h3 class="product-name" style="left:120px">Flowers</h3>
<h3 class="product-name" style="left:450px">Chocolate</h3>
<h3 class="product-name" style="left:780px">Bananas</h3>
<p class="product-copy" style="left:120px">Curabitur vel dolor ultrices ipsum dictum tristique Praesent vitae lacus Ut velit enim vestibulum non fermentum nec</p>
<p class="product-copy" style="left:450px">Curabitur vel dolor ultrices ipsum dictum tristique Praesent vitae lacus Ut velit enim vestibulum non fermentum nec</p>
<p class="product-copy" style="left:780px">Curabitur vel dolor ultrices ipsum dictum tristique Praesent vitae lacus Ut velit enim vestibulum non fermentum nec</p>
<a class="btn" href="#" style="left:189px;top:1355px;width:167px;height:45px;font-size:17px">Learn More</a>
<a class="btn" href="#" style="left:519px;top:1355px;width:167px;height:45px;font-size:17px">Learn More</a>
<a class="btn" href="#" style="left:849px;top:1355px;width:167px;height:45px;font-size:17px">Learn More</a>

<svg class="abs" style="left:0;top:1413px" width="1200" height="710" viewBox="0 0 1200 710">
  <defs><linearGradient id="benefitsFill" x1="0" y1="0" x2="1" y2="1"><stop offset="0" stop-color="#52c112"/><stop offset="1" stop-color="#2a7e00"/></linearGradient></defs>
  <path fill="url(#benefitsFill)" d="M0,0 Q300,90 570,107 L592,122 L608,122 L630,107 Q900,90 1200,0 L1200,690 Q600,600 0,700 Z"/>
  <polyline points="586,106 593,113 600,106" fill="none" stroke="#9a9a9a" stroke-width="1.5"/>
</svg>
<h2 class="section-title benefits-title">Featured Benefits</h2>

<div class="benefit-icon" style="left:134px;top:1652px"><svg width="46" height="46" viewBox="0 0 46 46" fill="none" stroke="#fff" stroke-width="2"><circle cx="23" cy="23" r="20" stroke-dasharray="3 3"/><polyline points="23,11 23,24 31,28"/></svg></div>
<div class="benefit-icon" style="left:633px;top:1652px"><svg width="50" height="36" viewBox="0 0 50 36" fill="none" stroke="#fff" stroke-width="2"><rect x="2" y="6" width="28" height="20" rx="2"/><path d="M30 12h10l7 8v6H30z"/><circle cx="12" cy="29" r="4"/><circle cx="38" cy="29" r="4"/></svg></div>
<div class="benefit-icon" style="left:134px;top:1830px"><svg width="40" height="46" viewBox="0 0 40 46" fill="none" stroke="#fff" stroke-width="2"><circle cx="20" cy="18" r="15"/><polygon points="20,9 23,15 29,16 24,20 26,26 20,23 14,26 16,20 11,16 17,15"/><path d="M12 31l-4 13 6-3 4 5 2-10M28 31l4 13-6-3-4 5-2-10"/></svg></div>
<div class="benefit-icon" style="left:633px;top:1830px"><svg width="44" height="46" viewBox="0 0 44 46" fill="none" stroke="#fff" stroke-width="2"><path d="M14 6h14l-3 6h-8z"/><path d="M17 12C8 18 8 32 21 32s13-14 4-20"/><path d="M2 34h10l8 5h14l8-5M2 42h40"/><text x="17" y="27" fill="#fff" stroke="none" font-size="12" font-family="Lato,sans-serif">$</text></svg></div>

<h3 class="benefit-name" style="left:238px;top:1659px">24/7 Available</h3>
<h3 class="benefit-name" style="left:740px;top:1659px">Free Shipping</h3>
<h3 class="benefit-name" style="left:238px;top:1835px">Quality Product</h3>
<h3 class="benefit-name" style="left:740px;top:1835px">Save Cost</h3>
<p class="benefit-copy" style="left:238px;top:1698px">convallis et vehicula ut pulvinar eu ante Integer orci tellus tristique vitae consequat nec porta vel lectus Nulla sit amet diam aliquam enim</p>
<p class="benefit-copy" style="left:740px;top:1698px">convallis et vehicula ut pulvinar eu ante Integer orci tellus tristique vitae consequat nec porta vel lectus Nulla sit amet diam aliquam enim</p>
<p class="benefit-copy" style="left:238px;top:1874px">convallis et vehicula ut pulvinar eu ante Integer orci tellus tristique vitae consequat nec porta vel lectus Nulla sit amet diam aliquam enim</p>
<p class="benefit-copy" style="left:740px;top:1874px">convallis et vehicula ut pulvinar eu ante Integer orci tellus tristique vitae consequat nec porta vel lectus Nulla sit amet diam aliquam enim</p>

<div class="abs" style="left:0;top:2113px;width:1200px;height:517px;background:linear-gradient(180deg,#ffffff 0%,#f2f3f4 60%,#ffffff 100%);z-index:-1"></div>
<div class="why-photo"><div role="img" aria-label="Crates of green bananas wrapped in purple packing"></div></div>
<h2 class="why-title">Why Choose Us</h2>
<p class="why-copy">Fusce tellus Sed metus augue convallis et vehicula ut pulvinar eu ante Integer orci tellus tristique vitae consequat nec porta</p>

<div class="why-item" style="left:641px;top:2307px"><svg width="18" height="18" viewBox="0 0 18 18" fill="none" stroke="#4db811" stroke-width="2"><circle cx="9" cy="9" r="7.5"/><polyline points="5,9 8,12 13,6"/></svg><b>Nulla sit amet</b><p>diam aliquam enim Proin dui lectus cursus eu mattis</p></div>
<div class="why-item" style="left:879px;top:2307px"><svg width="18" height="18" viewBox="0 0 18 18" fill="none" stroke="#4db811" stroke-width="2"><circle cx="9" cy="9" r="7.5"/><polyline points="5,9 8,12 13,6"/></svg><b>Augiat in pede Fusce</b><p>diam aliquam enim Proin dui lectus cursus eu mattis</p></div>
<div class="why-item" style="left:641px;top:2408px"><svg width="18" height="18" viewBox="0 0 18 18" fill="none" stroke="#4db811" stroke-width="2"><circle cx="9" cy="9" r="7.5"/><polyline points="5,9 8,12 13,6"/></svg><b>Curabitur iaculis</b><p>diam aliquam enim Proin dui lectus cursus eu mattis</p></div>
<div class="why-item" style="left:879px;top:2408px"><svg width="18" height="18" viewBox="0 0 18 18" fill="none" stroke="#4db811" stroke-width="2"><circle cx="9" cy="9" r="7.5"/><polyline points="5,9 8,12 13,6"/></svg><b>Sed metus auguee</b><p>diam aliquam enim Proin dui lectus cursus eu mattis</p></div>
<a class="btn" href="#" style="left:609px;top:2502px;width:166px;height:45px;font-size:17px">Learn More</a>

<section class="blogs"></section>
<h2 class="blogs-title">Recent Blogs</h2>
<div class="blog-photo" role="img" aria-label="Chocolatiers at work in a kitchen" style="left:136px;background:linear-gradient(135deg,#d8d8d8,#8a8480 60%,#4a3a30)"></div>
<div class="blog-photo" role="img" aria-label="Boxes of pink and orange roses at a flower market" style="left:456px;background:linear-gradient(135deg,#c8443a,#e070a8 50%,#5a5048)"></div>
<div class="blog-photo" role="img" aria-label="Banana bunch hanging on a tree against blue sky" style="left:777px;background:linear-gradient(180deg,#3a78c8,#5a9a3a 60%,#2f5a1a)"></div>
<article class="blog-card" style="left:157px"><div class="blog-date">13 JAN 2020</div><div class="blog-head">Augiat in pede Fusce tellus<br>Sed metus augue</div><p class="blog-copy">Morbi eget arcu Morbi porta libero id ullamcorper nonummy nibh</p><div class="blog-more">READ MORE</div></article>
<article class="blog-card" style="left:477px"><div class="blog-date">10 JAN 2020</div><div class="blog-head">Augiat in pede Fusce tellus<br>Sed metus augue</div><p class="blog-copy">Morbi eget arcu Morbi porta libero id ullamcorper nonummy nibh</p><div class="blog-more">READ MORE</div></article>
<article class="blog-card" style="left:798px"><div class="blog-date">05 JAN 2020</div><div class="blog-head">Augiat in pede Fusce tellus<br>Sed metus augue</div><p class="blog-copy">Morbi eget arcu Morbi porta libero id ullamcorper nonummy nibh</p><div class="blog-more">READ MORE</div></article>

<footer class="site-footer">
  <h4 class="foot-head" style="left:160px">MENU</h4>
  <ul class="foot-menu"><li>About Us</li><li>Our Services</li><li>Export</li><li>Testimonials</li><li>Blogs</li><li>Contact Us</li></ul>

  <h4 class="foot-head" style="left:332px">CONTACT US</h4>
  <div class="contact-row" style="top:114px"><i><svg width="14" height="18" viewBox="0 0 14 18"><path fill="#fff" d="M7 0a7 7 0 0 0-7 7c0 5 7 11 7 11s7-6 7-11a7 7 0 0 0-7-7zm0 10a3 3 0 1 1 0-6 3 3 0 0 1 0 6z"/></svg></i><span>48 Orchard Lane #4B<br>Riverton 20417 RV</span></div>
  <div class="contact-row" style="top:166px"><i><svg width="16" height="16" viewBox="0 0 16 16"><path fill="#fff" d="M3 1l3 3-2 2c1 2 3 4 5 5l2-2 3 3-2 3C7 15 1 9 1 3z"/></svg></i><span>Call Us<br>555.014.2736</span></div>
  <div class="contact-row" style="top:218px"><i><svg width="16" height="12" viewBox="0 0 16 12"><rect width="16" height="12" fill="#fff"/><polyline points="0,0 8,7 16,0" fill="none" stroke="#4db811" stroke-width="1.5"/></svg></i><span>Email Us<br>hello@verdanta-export.com</span></div>

  <h4 class="foot-head" style="left:619px">GET UPDATES</h4>
  <p class="foot-sub">Subscribe for Our Newsletters</p>
  <div class="foot-input">ENTER EMAIL ADDRESS</div>
  <div class="foot-btn">SUBSCRIBE</div>

  <h4 class="foot-head" style="left:906px">GET IN TOUCH</h4>
  <div class="social" style="top:108px"><i></i><div><small>Like us on</small><span>Facenote</span></div></div>
  <div class="social" style="top:160px"><i></i><div><small>Follow us on</small><span>Chirper</span></div></div>
  <div class="social" style="top:212px"><i></i><div><small>Follow us on</small><span>LinkLoop</span></div></div>
</footer>
<div class="copyright">Copyright © 2020 All right reserved</div>

</body>
</html>
```